"Career in Gradvel" | Poster design

We need a "We are hiring" poster design. We are a construction company based in Croatia and we are looking for 3 categories of construction workers. We want moder, serious and powerful poster . In attachment you can find our logo. The font of a text that is used in logo design is "nexa bold".

At the bottom (or where designer can see it) will be description of general condition. The poster must be simple and clear.

Target Market(s)

Wide range of employment

Industry/Entity Type

Construction Company

Colors

Designer to choose colors to be used in the design.

Requirements
Must have
• The text in poster that will be needed is "Mason/carpenter job", "Steel-bender job" and "Auxiliary worker". This terms may be wrong, but it will be translated in local language. Under all of them will be a short descrtiption row, and one row of salary. This is for all three categories.
• At the bottom (or where designer can see it) will be description of general condition. The poster must be simple and clear.

```html
<!DOCTYPE html>
<html lang="en">
<head>
<meta charset="utf-8">
<title>Gradvel – We Are Hiring</title>
<link rel="stylesheet" href="https://fonts.googleapis.com/css2?family=Bebas+Neue&family=Oswald:wght@500;600&family=Arimo:wght@400;700&family=Nunito+Sans:wght@800&display=swap">
<style>
  :root {
    --backdrop: #ffffff;
    --frame: #7b573a;
    --frame-dark: #6a4a30;
    --paper: #ead7b8;
    --paper-light: #f0e1c6;
    --accent: #c4651f;
    --accent-bright: #e07a2a;
    --ink: #3c3833;
    --rule: #4a4540;
  }
  * { margin: 0; padding: 0; box-sizing: border-box; }
  html, body { width: 849px; height: 1200px; overflow: hidden; background: var(--backdrop); }
  .poster { position: relative; width: 849px; height: 1200px; }
  .skyline {
    position: absolute; left: 88px; top: 22px; width: 690px; height: 128px;
    background: linear-gradient(180deg, #a07a58 0%, var(--frame) 100%);
  }
  .frame {
    position: absolute; left: 74px; top: 143px; width: 752px; height: 1028px;
    background: var(--frame);
  }
  .paper {
    position: absolute; left: 96px; top: 150px; width: 708px; height: 1000px;
    background: radial-gradient(ellipse at 50% 45%, var(--paper-light) 0%, var(--paper) 75%);
  }
  .brand { position: absolute; left: 0; right: 0; top: 191px; text-align: center; }
  .brand-mark {
    display: block; width: 48px; height: 48px; margin: 0 auto 6px;
    border: 2px solid var(--rule);
  }
  .brand-name {
    font-family: "Nunito Sans", sans-serif; font-weight: 800; font-size: 20px;
    letter-spacing: 1px; color: var(--accent-bright); line-height: 1;
  }
  .brand-tagline {
    font-family: "Arimo", sans-serif; font-size: 6.5px; letter-spacing: 0.3px;
    color: var(--ink); margin-top: 3px;
  }
  .headline {
    position: absolute; left: 0; right: 0; text-align: center;
    font-family: "Bebas Neue", sans-serif; color: var(--accent); line-height: 1;
  }
  .headline-top { top: 298px; font-size: 120px; }
  .headline-main { top: 398px; font-size: 240px; letter-spacing: -4px; }
  .jobs { position: absolute; left: 212px; width: 422px; top: 632px; text-align: center; }
  .job { padding: 4px 0 10px; }
  .job + .job { border-top: 2px dashed var(--rule); padding-top: 12px; }
  .job-title {
    font-family: "Bebas Neue", sans-serif; font-size: 36px; line-height: 32px;
    color: var(--accent); margin-bottom: 6px;
  }
  .job-text {
    font-family: "Arimo", sans-serif; font-weight: 700; font-size: 17px;
    line-height: 21.5px; color: var(--ink); white-space: nowrap;
  }
  .contact {
    position: absolute; left: 0; right: 0; top: 1003px; text-align: center;
    font-family: "Oswald", sans-serif; font-weight: 600; font-size: 27px;
    color: var(--accent); letter-spacing: 0.5px;
  }
  .terms {
    position: absolute; left: 113px; width: 622px; top: 1068px;
    font-family: "Arimo", sans-serif; font-size: 8.4px; line-height: 12.2px;
    color: var(--ink); text-align: justify;
  }
</style>
</head>
<body>
<main class="poster">
  <div class="skyline" role="img" aria-label="Brown city skyline silhouette with clouds along the top edge"></div>
  <div class="frame"></div>
  <div class="paper"></div>

  <header class="brand">
    <span class="brand-mark"></span>
    <div class="brand-name">GRADVEL</div>
    <div class="brand-tagline">IZVOĐENJE I VOĐENJE GRAĐEVINSKIH RADOVA</div>
  </header>

  <h1>
    <span class="headline headline-top">We Are</span>
    <span class="headline headline-main">Hiring</span>
  </h1>

  <section class="jobs">
    <article class="job">
      <h2 class="job-title">Mason/Carpenter Job</h2>
      <p class="job-text">of them of them Under all of theof them<br>m will be a short descrtiption row<br>Sallery $85000</p>
    </article>
    <article class="job">
      <h2 class="job-title">Steel-Bender Job</h2>
      <p class="job-text">of them of them Under all of theof them<br>m will be a short descrtiption row<br>Sallery $85000</p>
    </article>
    <article class="job">
      <h2 class="job-title">Auxiliary Worker</h2>
      <p class="job-text">of them of them Under all of theof them<br>m will be a short descrtiption row<br>Sallery $85000</p>
    </article>
  </section>

  <p class="contact">ph. 12345678910 &nbsp;|&nbsp; email:&nbsp; jobs@gradvel.com</p>

  <p class="terms">Terms &amp; Condations: is simply dummy text of the printing and typesetting industry. Lorem Ipsum has been the industry's standard dummy text ever since the 1500s, when an unknown printer took a galley of type and scrambled it to make a type specimen book. It has survived not only five centuries, but, remaining essentiTerms &amp; Condations: is simply dummy text of the printing and typesetting industry. Lorem Ipsum has been the industry's standard dummy text ever since the 1500s, when an unknown printer took a galley of type and scrambled it to make a type specimen book. It has survived not only five centuries, but, remaining essentially unchanged.ally unchanged.</p>
</main>
</body>
</html>
```